VORLAND COMPOSITES INC website in USA

VORLAND COMPOSITES INC incorporated and operated in USA needs a completely new design of website. This Wyoming based company is a importer and distributor of composites material to supply mainly to American and Canadian/Mexican customers. Our main products includes Carbon Fiber, Aramid Fiber, Glass Fiber, Basalt Fiber, High Silica Glass, Quartz Fiber, S-Glass, Alumina Fiber, Vacuum Auxiliary.

We are one stop composites solution provider for Automotive, Aerospace, Construction, Electrical and Machinery industries.

We are exclusive sales company in North America for BLORAN composites produced from China and their other Asia facilities.

Target Market(s)

USA and Canada

Industry/Entity Type

Composites materials

Coding

Coded - Design and coding required

Number of Pages Required

5+ page

Requirements
Nice to have
• Color theme to match our corporate logo VORLAND. VORLAND stands for Northgate Provisioning Trade Holdings

```html
<!DOCTYPE html>
<html lang="en">
<head>
<meta charset="utf-8">
<title>VORLAND COMPOSITES INC</title>
<link href="https://fonts.googleapis.com/css2?family=Archivo:wght@400;500;600;700;800&family=Oswald:wght@500;600&display=swap" rel="stylesheet">
<style>
:root{
  --orange:#f7941d;
  --dark:#3a322e;
  --ink:#1a1a1a;
  --text:#333;
  --muted:#555;
  --light:#f1f1f3;
  --white:#fff;
}
*{margin:0;padding:0;box-sizing:border-box}
html,body{width:1200px;height:3504px;overflow:hidden}
body{position:relative;font-family:'Archivo',sans-serif;color:var(--text);background:var(--white)}
.abs{position:absolute}
/* brand */
.brand{left:150px;top:28px;display:flex;align-items:center;gap:16px;width:300px}
.brand-main{display:flex;flex-direction:column;gap:4px}
.brand-row{display:flex;align-items:center;gap:7px}
.brand-mark{width:12px;height:12px;border-radius:50%;background:var(--orange);flex:none}
.brand-name{font-weight:800;font-size:33px;line-height:36px;color:var(--orange);letter-spacing:.5px}
.brand-tag{font-size:7px;line-height:9px;letter-spacing:1.6px;color:var(--ink);padding-left:19px;white-space:nowrap}
.brand-desc{border-left:2px solid var(--ink);padding:3px 0 3px 10px;font-size:10px;line-height:13px;color:var(--ink);width:108px}
/* header */
.phones{top:22px;left:745px;display:flex;gap:18px;align-items:center}
.phone-icon{width:26px;height:26px}
.phone{font-size:14px;color:var(--ink);line-height:18px}
.phone b{display:block;font-weight:500;font-size:17px}
.phone.usa{border-left:1px solid #999;padding-left:18px}
.nav{top:73px;left:556px;display:flex;gap:20px;font-size:15px;color:var(--ink);align-items:center}
.nav .active{background:var(--orange);color:var(--ink);border-radius:16px;padding:5px 12px}
/* hero */
.hero{left:0;top:124px;width:1200px;height:514px;background:radial-gradient(ellipse at 60% 30%,#5a5a5a,#2a2a2a 55%,#121212)}
.hero-title{top:212px;width:1200px;text-align:center;font-weight:700;font-size:52px;line-height:60px;color:var(--white)}
.hero-title span{color:var(--orange)}
.hero-sub{top:354px;left:320px;width:560px;text-align:center;font-size:20px;line-height:33px;color:var(--white)}
.hero-sub b{color:var(--orange)}
.btn{background:var(--orange);color:var(--ink);font-family:'Oswald',sans-serif;font-weight:600;border-radius:24px;display:flex;align-items:center;justify-content:center;text-transform:uppercase}
.hero-btn{left:528px;top:455px;width:144px;height:48px;font-size:18px}
.dots{top:578px;left:556px;display:flex;gap:11px}
.dots i{width:12px;height:12px;border-radius:50%;border:2px solid #fff;display:block}
.dots i.on{background:var(--orange);border-color:var(--orange)}
/* section heads */
.section-title{width:1200px;text-align:center;font-weight:700;font-size:34px;color:var(--ink)}
.rule{left:578px;width:44px;height:3px;background:var(--ink)}
.products-bg{left:0;top:638px;width:1200px;height:942px;background:#f7f7f7}
.tile{border-radius:8px;overflow:hidden}
.tile::after{content:"";position:absolute;left:0;right:0;bottom:0;height:60%;background:linear-gradient(to bottom,rgba(0,0,0,0),rgba(0,0,0,.55))}
.tile-label{position:absolute;z-index:1;left:22px;bottom:16px;color:var(--white);font-weight:600;font-size:20px}
.tile-body{position:absolute;z-index:1;left:20px;bottom:20px;color:var(--white)}
.tile-body h3{font-weight:600;font-size:20px}
.tile-body p{font-size:12px;line-height:14px;width:240px;margin:4px 0 12px}
.tile-body .btn{width:72px;height:22px;font-size:11px}
/* welcome */
.welcome-bg{left:0;top:1580px;width:1200px;height:454px;background:var(--dark)}
.welcome-img{left:0;top:1580px;width:571px;height:454px;background:linear-gradient(135deg,#555,#222 50%,#444);clip-path:ellipse(100% 120% at 0% 50%)}
.welcome-curve{left:0;top:1580px;width:590px;height:454px}
.welcome-title{left:638px;top:1622px;font-weight:700;font-size:34px;color:var(--white)}
.welcome-rule{left:644px;top:1688px;width:170px;height:2px;background:var(--white)}
.welcome-text{left:641px;top:1726px;width:410px;font-size:14px;line-height:19.5px;color:#ddd}
.welcome-btn{left:641px;top:1950px;width:132px;height:43px;font-size:17px}
/* why */
.why{top:2197px;width:240px;text-align:center}
.why-ring{width:126px;height:126px;margin:0 auto;border:2px solid var(--orange);border-radius:50%;display:flex;align-items:center;justify-content:center}
.why h3{margin-top:42px;font-weight:500;font-size:20px;color:var(--ink)}
.why p{margin-top:14px;font-size:14px;line-height:18px;color:var(--muted);padding:0 10px}
/* industries */
.industries-bg{left:0;top:2520px;width:1200px;height:677px;background:var(--light)}
/* footer */
.f-head{font-weight:700;font-size:13px;line-height:16px;color:var(--ink)}
.f-list{font-size:13px;line-height:18px;color:var(--muted)}
.f-list li{list-style:none}
.f-line{left:148px;top:3396px;width:904px;height:2px;background:var(--ink)}
.follow{left:148px;top:3434px;display:flex;align-items:center;gap:6px;font-weight:700;font-size:13px;color:var(--ink)}
.follow i{width:26px;height:26px;border-radius:50%;background:#2a2a2a;display:block}
.follow span{margin-right:8px}
.copy{right:148px;top:3438px;font-size:13px;color:var(--muted)}
</style>
</head>
<body>

<header>
  <div class="abs brand">
    <div class="brand-main">
      <div class="brand-row"><span class="brand-mark"></span><span class="brand-name">VORLAND</span></div>
      <div class="brand-tag">YOUR BRIDGE TO ASIA</div>
    </div>
    <div class="brand-desc">Northgate Provisioning Trade Holdings</div>
  </div>
  <div class="abs phones">
    <svg class="phone-icon" viewBox="0 0 24 24" fill="none" stroke="#1a1a1a" stroke-width="1.6"><circle cx="12" cy="12" r="11"/><path d="M8 6.5l2 2.5-1.2 1.5c.8 1.8 2 3 3.7 3.7L14 12.5l2.5 2-1 2c-4 0-8.5-4.5-8.5-8.5z"/></svg>
    <div class="phone">Canada<b>416-555-0187</b></div>
    <div class="phone usa">USA<b>307-555-0142</b></div>
  </div>
  <nav class="abs nav">
    <span class="active">Home</span><span>About Us</span><span>Products</span><span>Services</span><span>Industries</span><span>Contact Us</span>
  </nav>
</header>

<section>
  <div class="abs hero" role="img" aria-label="Close-up of woven carbon fiber fabric draped in folds"></div>
  <h1 class="abs hero-title"><span>Building Strength</span> with<br>Advanced Composites</h1>
  <p class="abs hero-sub">VORLAND Composites Inc – USA-based supplier of <b>premium fiber materials</b> for North American industries.</p>
  <a class="abs btn hero-btn">Read More</a>
  <div class="abs dots"><i class="on"></i><i></i><i></i><i></i></div>
</section>

<section>
  <div class="abs products-bg"></div>
  <h2 class="abs section-title" style="top:688px">OUR PRODUCTS</h2>
  <div class="abs rule" style="top:750px"></div>

  <div class="abs tile" style="left:150px;top:801px;width:292px;height:229px;background:linear-gradient(135deg,#5a5a5a,#1a1a1a 55%,#050505)" role="img" aria-label="Carbon fiber honeycomb material">
    <div class="tile-body"><h3>Carbon Fiber</h3><p>Lorem Ipsum is simply dummy text of the printing and typesetting industry</p><a class="btn">Read More</a></div>
  </div>
  <div class="abs tile" style="left:454px;top:801px;width:292px;height:229px;background:linear-gradient(160deg,#efe3c6,#c9aa74 55%,#8a6c40)" role="img" aria-label="Aramid fiber woven fabric"><span class="tile-label">Aramid Fiber</span></div>
  <div class="abs tile" style="left:756px;top:801px;width:293px;height:229px;background:linear-gradient(150deg,#e6e6e6,#a8a8a8 55%,#6e6e6e)" role="img" aria-label="Glass fiber woven cloth"><span class="tile-label">Glass Fiber</span></div>

  <div class="abs tile" style="left:150px;top:1043px;width:292px;height:229px;background:linear-gradient(150deg,#f2f2f2,#8a8a8a 50%,#2a2a2a)" role="img" aria-label="Roll of basalt fiber fabric"><span class="tile-label">Basalt Fiber</span></div>
  <div class="abs tile" style="left:454px;top:1043px;width:292px;height:229px;background:linear-gradient(150deg,#d8dee2,#8c989f 55%,#4a5660)" role="img" aria-label="High silica glass mesh"><span class="tile-label">High Silica Glass</span></div>
  <div class="abs tile" style="left:756px;top:1043px;width:293px;height:229px;background:linear-gradient(150deg,#e2dacd,#a89e8e 55%,#5e564b)" role="img" aria-label="Quartz fiber cloth"><span class="tile-label">Quartz Fiber</span></div>

  <div class="abs tile" style="left:150px;top:1286px;width:292px;height:229px;background:linear-gradient(150deg,#f2c478,#eeeeee 50%,#8a8a8a)" role="img" aria-label="Roll of S-glass fabric"><span class="tile-label">S-Glass</span></div>
  <div class="abs tile" style="left:454px;top:1286px;width:292px;height:229px;background:linear-gradient(160deg,#bcbcbc,#8a8a8a 55%,#4e4e4e)" role="img" aria-label="Alumina fiber mesh texture"><span class="tile-label">Alumina Fiber</span></div>
  <div class="abs tile" style="left:756px;top:1286px;width:293px;height:229px;background:linear-gradient(150deg,#e4dccd,#b0a48f 55%,#5e5040)" role="img" aria-label="Vacuum auxiliary twill fabric"><span class="tile-label">Vacuum Auxiliary</span></div>
</section>

<section>
  <div class="abs welcome-bg"></div>
  <div class="abs welcome-img" role="img" aria-label="Rolls of carbon fiber tape on woven carbon cloth"></div>
  <svg class="abs welcome-curve" viewBox="0 0 590 454"><path d="M470 0 C600 120 600 330 540 454 L560 454 C620 330 620 120 500 0 Z" fill="#f7941d"/></svg>
  <h2 class="abs welcome-title">WELCOME TO VORLAND</h2>
  <div class="abs welcome-rule"></div>
  <p class="abs welcome-text">Sed ut perspiciatis unde omnis iste natus error sit voluptatem accusantium doloremque laudantium, totam rem aperiam, eaque ipsa quae ab illo inventore veritatis et quasi architecto beatae vitae dicta sunt explicabo. Nemo enim ipsam voluptatem quia voluptas sit aspernatur aut odit aut fugit, sed quia consequuntur magni dolores eos qui ratione voluptatem sequi nesciunt. Neque porro quisquam est, qui dolorem ipsum quia dolor sit amet, consectetur, adipisci velit, sed quia non numquam eius modi tempora incidunt ut labore et dolore magnam aliquam quaerat voluptatem. Ut enim ad minima veniam.</p>
  <a class="abs btn welcome-btn">Read More</a>
</section>

<section>
  <h2 class="abs section-title" style="top:2082px">WHY CHOOSE US</h2>
  <div class="abs rule" style="top:2153px"></div>
  <div class="abs why" style="left:122px">
    <div class="why-ring"><svg width="56" height="56" viewBox="0 0 24 24" fill="none" stroke="#f7941d" stroke-width="1.1"><circle cx="12" cy="12" r="9"/><circle cx="12" cy="12" r="5.5"/><path d="M9.5 12l1.8 1.8 3.2-3.4"/></svg></div>
    <h3>Quality</h3><p>Sed ut perspiciatis unde omnis iste natus error sit voluptatem accusantium doloremque la uda ntium, totam rem.</p>
  </div>
  <div class="abs why" style="left:358px">
    <div class="why-ring"><svg width="56" height="56" viewBox="0 0 24 24" fill="none" stroke="#f7941d" stroke-width="1.1"><circle cx="12" cy="10" r="4"/><path d="M12 8v4M3 18c3-2 5-2 8-1h4l5-3"/><path d="M6 8V3M4 5l2-2 2 2M18 8V3M16 5l2-2 2 2"/></svg></div>
    <h3>Cost Effective</h3><p>Sed ut perspiciatis unde omnis iste natus error sit voluptatem accusantium doloremque la uda ntium, totam rem.</p>
  </div>
  <div class="abs why" style="left:601px">
    <div class="why-ring"><svg width="56" height="56" viewBox="0 0 24 24" fill="none" stroke="#f7941d" stroke-width="1.1"><circle cx="10" cy="12" r="7"/><path d="M13 9h5v6h-5zM15 18.5l1.3 1.3 2.5-2.6"/></svg></div>
    <h3>Reliable</h3><p>Sed ut perspiciatis unde omnis iste natus error sit voluptatem accusantium doloremque la uda ntium, totam rem.</p>
  </div>
  <div class="abs why" style="left:839px">
    <div class="why-ring"><svg width="56" height="56" viewBox="0 0 24 24" fill="none" stroke="#f7941d" stroke-width="1.1"><circle cx="12" cy="12" r="8"/><circle cx="12" cy="12" r="4.5"/><circle cx="12" cy="12" r="2"/></svg></div>
    <h3>Service</h3><p>Sed ut perspiciatis unde omnis iste natus error sit voluptatem accusantium doloremque la uda ntium, totam rem.</p>
  </div>
</section>

<section>
  <div class="abs industries-bg"></div>
  <h2 class="abs section-title" style="top:2565px">INDUSTRIES WE SERVE</h2>
  <div class="abs rule" style="top:2634px"></div>
  <div class="abs tile" style="left:150px;top:2672px;width:292px;height:230px;background:linear-gradient(160deg,#a8b2bc,#5e6872 55%,#2a3038)" role="img" aria-label="Automotive assembly line"><span class="tile-label">Automotive</span></div>
  <div class="abs tile" style="left:454px;top:2672px;width:292px;height:230px;background:linear-gradient(160deg,#8eb8dc,#4a7498 55%,#1e3448)" role="img" aria-label="Aircraft in a hangar"><span class="tile-label">Aerospace</span></div>
  <div class="abs tile" style="left:756px;top:2672px;width:293px;height:230px;background:linear-gradient(180deg,#8cc0ec,#b8c8d4 35%,#c09060 65%,#5a4330)" role="img" aria-label="Building under construction with crane"><span class="tile-label">Construction</span></div>
  <div class="abs tile" style="left:150px;top:2916px;width:445px;height:230px;background:linear-gradient(150deg,#c8b8a8,#7a6a5c 55%,#3c3430)" role="img" aria-label="Electrician testing a switchboard"><span class="tile-label">Electrical</span></div>
  <div class="abs tile" style="left:605px;top:2916px;width:444px;height:230px;background:linear-gradient(150deg,#8a8a90,#3a3a3e 55%,#a06030)" role="img" aria-label="Factory floor with industrial machines"><span class="tile-label">Machinery industries</span></div>
</section>

<footer>
  <div class="abs brand" style="top:3268px">
    <div class="brand-main">
      <div class="brand-row"><span class="brand-mark"></span><span class="brand-name">VORLAND</span></div>
      <div class="brand-tag">YOUR BRIDGE TO ASIA</div>
    </div>
    <div class="brand-desc">Northgate Provisioning Trade Holdings</div>
  </div>
  <div class="abs" style="left:490px;top:3236px">
    <div class="f-head">MENU</div>
    <ul class="f-list" style="margin-top:8px"><li>Home</li><li>About Us</li><li>Products</li><li>Services</li><li>Industries</li><li>Contact Us</li></ul>
  </div>
  <div class="abs" style="left:590px;top:3236px;width:220px">
    <div class="f-head">USA</div>
    <div class="f-list" style="margin-top:8px">48 Larkspur Ave Ste 12, Ridgeford, WY, USA 82990</div>
    <div class="f-list" style="margin-top:8px">307-555-0142</div>
  </div>
  <div class="abs" style="left:838px;top:3236px;width:220px">
    <div class="f-head">CANADA</div>
    <div class="f-list" style="margin-top:8px">2150 Alderbrook Rd, Suite 300, Fenwick, ON, L9X 4K1, Canada</div>
    <div class="f-list" style="margin-top:8px">416-555-0187</div>
  </div>
  <div class="abs f-line"></div>
  <div class="abs follow"><span>FOLLOW US</span><i></i><i></i><i></i><i></i><i></i></div>
  <div class="abs copy">Copyright © 2025 All Rights Reserved</div>
</footer>

</body>
</html>
```